Custom Cabinet Shop Needs a website design

Hi,
We need a website for a Custom Cabinet Shop and Cabinet parts manufacturing business.
The business has two sides to it. One side provides custom Kitchens, vanities, entertainment units, offices and what not to homeowners and contractors.
The 2nd side of the business provides built to order cabinet boxes and other parts required to put together a project to other cabinet shops, small contractors looking to install there own cabinets.
Website will need a Gallery to display work.
Color scheme to go well with logo.
current website is www.brambleoakcustomcabinets.com
being changed to www.brambleoak.ca
Logo Included in attached files.
Tagline "Joinery with Spirit"
Mission Statement "Our passion is to deliver inspired cabinetry solutions to suit all your needs, supported by our phenomenal star class customer service"
The website should convey quality and professionalism.
Thank you.
Homeowners/ Contractors
Entertainment

```html
<!DOCTYPE html>
<html lang="en">
<head>
<meta charset="utf-8">
<title>Brambleoak Custom Cabinets</title>
<link href="https://fonts.googleapis.com/css2?family=Figtree:wght@400;600;700&display=swap" rel="stylesheet">
<style>
:root{
  --orange:#f05a22;
  --ink:#1e1e1e;
  --text:#555;
  --link:#a3300c;
  --band:#efefef;
  --footer:#262626;
  --footer-text:#c9c9c9;
  --line:#cfcfcf;
}
*{box-sizing:border-box;margin:0;padding:0}
html,body{width:1052px;height:1200px;overflow:hidden;background:#fff}
body{position:relative;font-family:"Figtree",Arial,sans-serif;color:var(--text)}
.abs{position:absolute}
.top-rule{left:0;top:0;width:1052px;height:3px;background:var(--orange)}
.brand{left:96px;top:38px;display:flex;align-items:center;gap:10px}
.brand-mark{width:26px;height:26px;border-radius:50%;background:var(--orange)}
.brand-name{font-size:22px;font-weight:700;color:var(--ink);letter-spacing:.5px}
.nav a{position:absolute;top:46px;height:29px;line-height:29px;font-size:13px;color:var(--ink);text-decoration:none;font-weight:600}
.nav .active{left:373px;width:52px;text-align:center;background:var(--orange);color:#fff}
.header-divider{left:772px;top:26px;width:1px;height:60px;background:var(--line)}
.header-phone{left:792px;top:46px;display:flex;align-items:center;gap:10px;font-size:21px;color:var(--ink);font-weight:600}

.hero{left:0;top:106px;width:1052px;height:462px;
  background:
    radial-gradient(ellipse 260px 200px at 960px 190px,rgba(240,244,236,.85),rgba(240,244,236,0) 70%),
    radial-gradient(ellipse 160px 70px at 650px 150px,rgba(255,250,235,.6),rgba(255,250,235,0) 70%),
    linear-gradient(180deg,#c9c2b6 0%,#b7ab9b 30%,#8c7a68 55%,#5f4f44 75%,#3e332d 100%)}
.hero-caption{left:97px;top:253px;width:291px;height:161px;background:rgba(235,235,235,.85);padding:18px 14px 0}
.hero-caption h1{font-size:28px;font-weight:600;color:var(--ink);line-height:1;margin-bottom:8px;white-space:nowrap;letter-spacing:-.3px}
.hero-caption h1 span{color:var(--orange)}
.hero-caption p{font-size:13px;line-height:16px;color:var(--ink);width:250px}
.hero-caption a{display:block;margin-top:8px;font-size:11px;color:var(--link);text-decoration:none}

.welcome{left:96px;top:603px;width:330px}
.welcome h2{font-size:25px;font-weight:700;color:var(--ink);line-height:28px;white-space:nowrap}
.welcome h2 span{color:var(--orange);display:block;font-size:23px}
.welcome p{font-size:12px;line-height:14px;margin-top:14px;width:315px}
.welcome a{display:inline-block;margin-top:16px;margin-left:2px;font-size:12px;color:var(--link);text-decoration:underline}
.welcome-photo{left:427px;top:608px;width:218px;height:218px;
  background:
    radial-gradient(ellipse 60px 40px at 40px 80px,rgba(250,240,225,.8),rgba(250,240,225,0) 70%),
    linear-gradient(180deg,#d8d2c8 0%,#9a8f85 30%,#3b2c26 55%,#2b211d 75%,#9a4e2a 100%)}

.question{left:670px;top:603px;width:300px}
.question h2{font-size:21px;font-weight:700;color:var(--ink)}
.question p{font-size:12px;line-height:14px;margin-top:6px;color:#444;width:275px}
.field{position:absolute;border:1px solid #c8c8c8;font-size:10px;font-style:italic;color:#999;padding:7px 6px;background:#fff}
.send{left:761px;top:796px;width:105px;height:29px;background:var(--orange);color:#fff;font-size:17px;font-weight:700;text-align:center;line-height:29px}

.gallery-band{left:0;top:863px;width:1052px;height:221px;background:var(--band)}
.gallery-head{left:96px;top:880px}
.gallery-head h2{font-size:21px;font-weight:700;color:var(--ink)}
.gallery-head p{font-size:12px;margin-top:2px}
.gallery-arrows{left:906px;top:895px;width:61px;height:26px;background:#fff;display:flex;justify-content:center;align-items:center;gap:2px}
.thumb{position:absolute;top:937px;width:153px;height:86px}
.thumb-1{border-left:2px solid var(--orange)}
.thumb-cap{position:absolute;top:1034px;font-size:11px;color:var(--link)}
.thumb-cap u{margin-right:5px}

.footer{left:0;top:1084px;width:1052px;height:116px;background:var(--footer)}
.footer-links{left:96px;top:1109px;font-size:12px;color:var(--footer-text)}
.footer-links span{margin:0 12px;color:#777}
.footer-contact{left:652px;top:1110px;display:flex;align-items:center;gap:8px;font-size:11px;color:var(--footer-text)}
.footer-rule{left:96px;top:1140px;width:860px;height:1px;background:#4a4a4a}
.copyright{left:96px;top:1162px;font-size:11px;color:var(--footer-text)}
.social{position:absolute;top:1155px;width:29px;height:29px;border-radius:3px;background:#6a6a6a;border:1px solid #7c7c7c}
</style>
</head>
<body>
<div class="abs top-rule"></div>

<header>
  <div class="abs brand"><div class="brand-mark"></div><span class="brand-name">BRAMBLEOAK</span></div>
  <nav class="nav">
    <a class="active" href="#">Home</a>
    <a style="left:447px" href="#">Gallery</a>
    <a style="left:517px" href="#">Services</a>
    <a style="left:597px" href="#">Warranty</a>
    <a style="left:680px" href="#">Contact</a>
  </nav>
  <div class="abs header-divider"></div>
  <div class="abs header-phone">
    <svg width="20" height="20" viewBox="0 0 24 24"><path fill="#f05a22" d="M6.6 10.8a15 15 0 0 0 6.6 6.6l2.2-2.2a1 1 0 0 1 1-.25 11.4 11.4 0 0 0 3.6.57 1 1 0 0 1 1 1V20a1 1 0 0 1-1 1A17 17 0 0 1 3 4a1 1 0 0 1 1-1h3.5a1 1 0 0 1 1 1c0 1.25.2 2.45.57 3.57a1 1 0 0 1-.25 1z"/></svg>
    403-555-0187
  </div>
</header>

<section>
  <div class="abs hero" role="img" aria-label="Photo of a finished kitchen with white cabinets, pendant lights and granite counters"></div>
  <div class="abs hero-caption">
    <h1>Joinery <span>with Spirit</span></h1>
    <p>Lorem ipsum dolor sit amet, consectetur adip iscing elit, sed do eiusmod incidid untut labore et doloreLorem ipsum dolor sit amet..</p>
    <a href="#">Why choose us &gt;&gt;</a>
  </div>
</section>

<section>
  <div class="abs welcome">
    <h2>Welcome <span>Brambleoak Custom Cabinets</span></h2>
    <p>Lorem ipsum dolor sit amet, consectetur adipiscing elit, sed do eiusmod tempor incididunt ut labore et dolore magna aliqua.</p>
    <p>Ut enim ad minim veniam, quis nostrud exercitation ullamco laboris nisi ut aliquip ex ea commodo consequat-Lorem ipsum dolor sit amet, consectetur adipiscing elit, sed do eiusmod tempor incididunt ut labore et dolore adipiscing elit, sed do eiusmod tempor incididunt ut.</p>
    <a href="#">Learn More About us &gt;&gt;</a>
  </div>
  <div class="abs welcome-photo" role="img" aria-label="Photo of a kitchen island with dark cabinetry, bar stools and pendant lights"></div>
  <div class="abs question">
    <h2>Do you have any question?</h2>
    <p>Feel free to ask any questions. We will try to<br>answer&nbsp; as soons as possible</p>
  </div>
  <div class="field" style="left:670px;top:670px;width:138px;height:26px">Your Name</div>
  <div class="field" style="left:817px;top:670px;width:138px;height:26px">Your Email</div>
  <div class="field" style="left:670px;top:705px;width:288px;height:82px;padding:10px">Your question</div>
  <div class="abs send">Send</div>
</section>

<section>
  <div class="abs gallery-band"></div>
  <div class="abs gallery-head">
    <h2>Our Gallery</h2>
    <p>Lorem ipsum dolor sit amet, consectetur adipiscing elit,</p>
  </div>
  <div class="abs gallery-arrows">
    <svg width="19" height="19" viewBox="0 0 20 20"><circle cx="10" cy="10" r="10" fill="#222"/><path d="M12 6v8l-5-4z" fill="#fff"/></svg>
    <svg width="19" height="19" viewBox="0 0 20 20"><circle cx="10" cy="10" r="10" fill="#222"/><path d="M8 6v8l5-4z" fill="#fff"/></svg>
  </div>
  <div class="thumb thumb-1" style="left:96px;background:linear-gradient(180deg,#3a2a24 0%,#5a3b2e 45%,#c9b59a 75%,#4a3128 100%)" role="img" aria-label="Photo of a dark wood bar cabinet"></div>
  <div class="thumb" style="left:271px;background:linear-gradient(180deg,#d9d6cf 0%,#b0aaa0 45%,#5f554c 75%,#3a302a 100%)" role="img" aria-label="Photo of a bright kitchen with bar stools"></div>
  <div class="thumb" style="left:448px;background:linear-gradient(180deg,#d7cabb 0%,#b5a08c 40%,#7a3a22 70%,#5a2a18 100%)" role="img" aria-label="Photo of a wood entertainment unit"></div>
  <div class="thumb" style="left:626px;background:linear-gradient(90deg,#3a4a52 0%,#8e9aa0 35%,#b4bec2 60%,#6e7c82 100%)" role="img" aria-label="Photo of built-in shelving"></div>
  <div class="thumb" style="left:803px;background:linear-gradient(180deg,#d8d2b8 0%,#a89370 40%,#5b3f2e 70%,#7a5238 100%)" role="img" aria-label="Photo of a dining nook with bench seating"></div>
  <div class="thumb-cap" style="left:96px"><u>Lorem Ipsum Dolor sit</u>(15)</div>
  <div class="thumb-cap" style="left:271px"><u>Lorem Ipsum Dolor sit</u>(15)</div>
  <div class="thumb-cap" style="left:447px"><u>Lorem Ipsum Dolor sit</u>(15)</div>
  <div class="thumb-cap" style="left:627px"><u>Lorem Ipsum Dolor sit</u>(15)</div>
  <div class="thumb-cap" style="left:802px"><u>Lorem Ipsum Dolor sit</u>(15)</div>
</section>

<footer>
  <div class="abs footer"></div>
  <div class="abs footer-links">Advice<span>|</span>About<span>|</span>Contact<span>|</span>Privacy Policy<span>|</span>Terms &amp; Conditons</div>
  <div class="abs footer-contact">
    <svg width="14" height="14" viewBox="0 0 24 24"><path fill="#aaa" d="M6.6 10.8a15 15 0 0 0 6.6 6.6l2.2-2.2a1 1 0 0 1 1-.25 11.4 11.4 0 0 0 3.6.57 1 1 0 0 1 1 1V20a1 1 0 0 1-1 1A17 17 0 0 1 3 4a1 1 0 0 1 1-1h3.5a1 1 0 0 1 1 1c0 1.25.2 2.45.57 3.57a1 1 0 0 1-.25 1z"/></svg>
    <span>403-555-0187</span>
    <svg width="15" height="12" viewBox="0 0 15 12" style="margin-left:6px"><rect x=".5" y=".5" width="14" height="11" fill="none" stroke="#aaa"/><path d="M.5.5l7 6 7-6" fill="none" stroke="#aaa"/></svg>
    <span>sales@brambleoakcustomcabinets.com</span>
  </div>
  <div class="abs footer-rule"></div>
  <div class="abs copyright">© 2015 Brambleoak Custom Cabinets. All rights reserved</div>
  <div class="social" style="left:822px" aria-label="Social profile"></div>
  <div class="social" style="left:868px" aria-label="Social profile"></div>
  <div class="social" style="left:914px" aria-label="Social profile"></div>
</footer>
</body>
</html>
```